A layout of a webpage for oil trade platform

I would like to have a desgin of one page webpage (with section scrollling dowin) that woulf present the new product i.e. oil trade platform for wholesale buyers and sellers.
Layout should consist of the sections similar to the given at: https://porada.leczmypol.pl/panel-planowania-spotkan
However oil industy require more colors and more photo stories than here for doctor.
I. I woul imagine at first below menu a slider with brueg information about the product and its advantages with "more" button next to the prict screen of our platform on different displays (PC and mobile).
II. Bellow the slider I would imagine icons correspoing to the advantages of that plaftorm:
1. Purchase/sale process automation 24/7
2. Access to the best deals
3. Electronic offerings and orderings
4. Transaction status monitoring
5. Data and transaction security
II A) (optional):
In near future we would like to prepare a short video presenation. Hence please prepare a place to display that element here.
At the moment alternatvily please prepare a How it works section that would explan the platform operating process
III. Next secion is about benefits for Oil Purchaser
It can be done either by icons of by text and corresponding grahip for while section.
Benefits:
- Access to cheaper oil
- Convenience of online orders
- Possibility to compare prices on the market
- Transaction history
- Order status monitoring
- Seccurity and transparency of purchase
IV. Next seciont is about benefits for Oil Seller
Benefits:
- New sale channel
- Attracting new clients
- More oil sold
- Transaction security
- Possibility to integrate with distribution infrastructure and logistits for more efficient automation.
V. Contact form
VI. Footer
I would need a layout that that will correspond to the very dynamic logo but I would expect also a clean form, smoth and modern. It has to be proffessional layout with more corporate character.
It can use a paralax features if needed.

```html
<!DOCTYPE html>
<html lang="en">
<head>
<meta charset="utf-8">
<title>Crudeline – Oil Trade Platform</title>
<link rel="stylesheet" href="https://fonts.googleapis.com/css2?family=Lato:wght@300;400;700&family=Open+Sans:wght@400;600&display=swap">
<style>
:root{
  --orange:#e4572e;
  --orange-deep:#e0501f;
  --navy:#1c2340;
  --navy-deep:#161c36;
  --ink:#2a2f45;
  --text:#555a66;
  --muted:#8a8f99;
  --grey-band:#ececec;
  --field:#ebebeb;
  --field-line:#c9c9c9;
  --white:#ffffff;
}
*{box-sizing:border-box;margin:0;padding:0}
html,body{width:1200px;height:3186px;overflow:hidden;background:var(--white)}
body{font-family:"Open Sans",sans-serif;color:var(--text);position:relative}
.heading{font-family:"Lato",sans-serif;font-weight:300}

/* header */
.site-header{position:absolute;top:0;left:0;width:1200px;height:102px;background:var(--white);display:flex;align-items:center;justify-content:space-between;padding:0 92px 0 123px}
.brand{display:flex;align-items:center;gap:14px;font-family:"Lato",sans-serif;font-weight:700;font-size:34px;color:var(--navy);letter-spacing:.5px}
.brand-dot{width:44px;height:44px;border-radius:50%;background:var(--orange)}
.main-nav{display:flex;gap:30px;font-family:"Lato",sans-serif;font-size:16px;color:var(--ink)}
.main-nav .active{color:var(--orange)}

/* hero */
.hero{position:absolute;top:102px;left:0;width:1200px;height:544px;background:linear-gradient(180deg,#1f2745 0%,#3a2c45 35%,#b4462e 75%,#e4572e 100%)}
.hero-copy{position:absolute;left:110px;top:158px;width:420px;color:var(--white)}
.hero-title{font-size:38px;line-height:44px;font-weight:400;white-space:nowrap}
.hero-sub{font-size:31px;line-height:36px;font-weight:400;white-space:nowrap}
.hero-text{margin-top:18px;font-size:13px;line-height:22px;color:#f0dcd4}
.btn-outline{display:inline-block;margin-top:20px;width:140px;height:40px;border:2px solid var(--white);color:var(--white);font-family:"Lato",sans-serif;font-size:18px;text-align:center;line-height:36px}
.device-showcase{position:absolute;left:545px;top:98px;width:560px;height:330px;border-radius:6px;background:linear-gradient(160deg,#2a2f3e 0%,#3d4252 55%,#5a4a4a 100%)}
.slider-dots{position:absolute;top:506px;left:544px;display:flex;gap:8px}
.slider-dots span{width:20px;height:3px;background:rgba(255,255,255,.75)}
.slider-dots .on{background:var(--navy)}

/* features */
.features{position:absolute;top:646px;left:0;width:1200px;height:212px}
.feature{position:absolute;width:200px;text-align:center;padding-top:32px}
.feature svg{display:block;margin:0 auto 16px}
.feature p{font-size:16px;line-height:26px;color:var(--text)}

/* how it works */
.how{position:absolute;top:858px;left:0;width:1200px;height:448px;background:var(--grey-band)}
.how-copy{position:absolute;left:112px;top:70px;width:440px}
.section-title{font-size:34px;color:var(--ink);font-weight:400}
.how-copy p{margin-top:14px;font-size:13px;line-height:24px;color:var(--text)}
.btn-solid{display:inline-block;margin-top:24px;width:142px;height:42px;background:var(--orange);color:var(--white);font-size:14px;text-align:center;line-height:42px}
.video{position:absolute;left:603px;top:62px;width:487px;height:300px;background:linear-gradient(180deg,#8aa3bf 0%,#5e6f87 45%,#2f3645 100%)}
.video-play{position:absolute;left:195px;top:102px}

/* benefits purchaser */
.benefits{position:absolute;top:1306px;left:0;width:1200px;height:584px}
.benefits .section-title{position:absolute;top:50px;width:100%;text-align:center;color:var(--orange);font-size:31px}
.benefit{position:absolute;width:480px;display:flex;gap:22px}
.benefit svg{flex:none}
.benefit h3{font-family:"Lato",sans-serif;font-weight:400;font-size:19px;color:var(--ink);margin-bottom:8px;white-space:nowrap}
.benefit p{font-size:12px;line-height:21px;color:var(--muted);width:380px}

/* seller */
.seller{position:absolute;top:1890px;left:0;width:1200px;height:448px}
.seller-panel{position:absolute;left:0;top:0;width:603px;height:448px;background:var(--orange-deep);color:var(--white);padding:62px 40px 0 119px}
.seller-panel h2{font-size:32px;font-weight:400}
.seller-panel .lead{margin-top:12px;font-size:13px;line-height:22px;color:#fbe3da}
.seller-list{list-style:none;margin-top:16px}
.seller-list li{position:relative;padding-left:28px;font-size:14px;font-weight:600;line-height:21px;margin-bottom:11px}
.seller-list li::before{content:"";position:absolute;left:2px;top:6px;border-left:9px solid var(--white);border-top:5px solid transparent;border-bottom:5px solid transparent}
.seller-photo{position:absolute;left:603px;top:0;width:597px;height:448px;background:linear-gradient(180deg,#6c7480 0%,#a08a6a 45%,#d9a24a 62%,#3b3f45 100%)}

/* contact */
.contact{position:absolute;top:2338px;left:0;width:1200px;height:504px}
.contact .section-title{position:absolute;top:68px;width:100%;text-align:center;font-size:32px}
.field{position:absolute}
.field label{display:block;font-size:13px;color:var(--text);margin-bottom:6px}
.field .box{width:100%;height:43px;background:var(--field);border:1px solid var(--field-line)}
.field .box.tall{height:106px}
.btn{position:absolute;top:372px;height:45px;color:var(--white);font-size:16px;text-align:center;line-height:45px}
.btn-submit{left:442px;width:155px;background:var(--orange)}
.btn-reset{left:605px;width:155px;background:var(--navy)}

/* footer */
.site-footer{position:absolute;top:2842px;left:0;width:1200px;height:344px;background:var(--navy-deep);color:#cdd1de}
.footer-col{position:absolute;top:68px}
.footer-col h4{font-family:"Lato",sans-serif;font-weight:400;font-size:21px;color:var(--white);margin-bottom:14px}
.footer-col li{list-style:none;font-size:13px;line-height:30px}
.socials{display:flex;gap:7px;margin-top:10px}
.socials span{width:30px;height:30px;border:1.5px solid #cdd1de;border-radius:50%}
.footer-brand{position:absolute;left:878px;top:110px;color:var(--white);font-size:32px}
.footer-brand .brand-dot{width:40px;height:40px}
.footer-legal{position:absolute;left:824px;top:170px;width:280px;text-align:center;font-size:12px;line-height:28px}
</style>
</head>
<body>

<header class="site-header">
  <div class="brand"><span class="brand-dot"></span>Crudeline</div>
  <nav class="main-nav">
    <span class="active">HOME</span><span>ABOUT US</span><span>SERVICES</span><span>BENEFITS</span><span>HOW IT WORKS</span><span>CONTACT</span>
  </nav>
</header>

<section class="hero">
  <div class="hero-copy">
    <h1 class="heading hero-title">Etiam eleifend metus vitae</h1>
    <p class="heading hero-sub">adipiscing semper mauris</p>
    <p class="hero-text">Maecenas aliquet velit vel turpis Mauris neque metus malesuada nec ultricies sit amet porttitor mattis enim In massa libero interdum nec interdum vel blandit sed nulla</p>
    <span class="btn-outline">MORE</span>
  </div>
  <div class="device-showcase" role="img" aria-label="Screenshot of the trading platform dashboard shown on desktop monitor, laptop, tablet and phone"></div>
  <div class="slider-dots"><span></span><span></span><span class="on"></span><span></span></div>
</section>

<section class="features">
  <div class="feature" style="left:106px">
    <svg width="66" height="66" viewBox="0 0 66 66" fill="none" stroke="var(--orange)" stroke-width="2"><circle cx="33" cy="33" r="30"/><circle cx="33" cy="33" r="22"/><path d="M22 42 V32 M30 42 V26 M38 42 V30 M46 42 V22 M20 44 H48"/></svg>
    <p>Purchase/sale process<br>automation 24/7</p>
  </div>
  <div class="feature" style="left:299px">
    <svg width="66" height="66" viewBox="0 0 66 66" fill="none" stroke="var(--orange)" stroke-width="2"><path d="M14 18 H32 L52 38 L38 52 L18 32 Z"/><circle cx="24" cy="26" r="3"/><path d="M30 34 L40 44"/></svg>
    <p>Access to the<br>best deals</p>
  </div>
  <div class="feature" style="left:469px">
    <svg width="66" height="66" viewBox="0 0 66 66" fill="none" stroke="var(--orange)" stroke-width="2"><circle cx="33" cy="30" r="12"/><circle cx="33" cy="30" r="5"/><path d="M33 14 V8 M33 46 V58 M17 30 H10 M49 30 H56 M21 42 L14 52 M45 42 L52 52 M21 18 L15 12 M45 18 L51 12"/><circle cx="33" cy="60" r="2"/><circle cx="13" cy="54" r="2"/><circle cx="53" cy="54" r="2"/></svg>
    <p>Electronic offerings<br>and orderings</p>
  </div>
  <div class="feature" style="left:703px">
    <svg width="66" height="66" viewBox="0 0 66 66"><rect x="10" y="14" width="46" height="30" fill="var(--orange)"/><rect x="14" y="18" width="38" height="22" fill="#fff"/><rect x="18" y="22" width="30" height="14" fill="var(--orange)"/><rect x="29" y="44" width="8" height="8" fill="var(--orange)"/><rect x="22" y="52" width="22" height="3" fill="var(--orange)"/></svg>
    <p>Transaction Status<br>monitoring</p>
  </div>
  <div class="feature" style="left:892px">
    <svg width="66" height="66" viewBox="0 0 66 66" fill="none" stroke="var(--orange)" stroke-width="2"><circle cx="33" cy="33" r="22"/><path d="M33 10 V4 M33 56 V62 M10 33 H4 M56 33 H62"/><path d="M33 20 L44 24 V34 C44 41 39 45 33 48 C27 45 22 41 22 34 V24 Z"/><path d="M28 34 L32 38 L39 29"/></svg>
    <p>Data and transaction<br>security</p>
  </div>
</section>

<section class="how">
  <div class="how-copy">
    <h2 class="heading section-title">How it works</h2>
    <p>Maecenas aliquet velit vel turpis Mauris neque metus malesuada nec ultricies sit amet porttitor mattis enim In massa libero interdum nec interdum vel blandit sed nulla In ullamcorper est eget tempor cursus neque mi consectetuer mi a</p>
    <p>Class aptent taciti sociosqu ad litora torquent per conubia nostra per inceptos hymenaeos Proin nulla arcu nonummy</p>
    <span class="btn-solid">READ MORE</span>
  </div>
  <div class="video" role="img" aria-label="Video presentation: oil rig crew standing on a drilling platform against the sky">
    <svg class="video-play" width="96" height="96" viewBox="0 0 96 96" fill="none"><circle cx="48" cy="48" r="45" stroke="#fff" stroke-width="3"/><path d="M38 30 L66 48 L38 66 Z" fill="#fff"/></svg>
  </div>
</section>

<section class="benefits">
  <h2 class="heading section-title">Benefits for Oil Purchaser</h2>

  <div class="benefit" style="left:132px;top:148px">
    <svg width="44" height="48" viewBox="0 0 44 48" fill="none" stroke="var(--navy)" stroke-width="2.4"><path d="M22 4 C14 18 9 24 9 32 A13 13 0 0 0 35 32 C35 24 30 18 22 4 Z"/><path d="M16 34 A6 6 0 0 0 22 40"/></svg>
    <div><h3>Access to cheaper Oil</h3><p>Class aptent taciti sociosqu ad litora torquent per conubia nostra per inceptos hymenaeos Proin nulla</p></div>
  </div>
  <div class="benefit" style="left:655px;top:148px">
    <svg width="44" height="48" viewBox="0 0 44 48" fill="none" stroke="var(--navy)" stroke-width="2.4"><path d="M8 14 A18 18 0 1 1 4 26"/><path d="M4 8 V16 H12"/><path d="M22 14 V26 H30"/></svg>
    <div><h3>Transaction history</h3><p>Class aptent taciti sociosqu ad litora torquent per conubia nostra per inceptos hymenaeos Proin nulla</p></div>
  </div>
  <div class="benefit" style="left:132px;top:275px">
    <svg width="44" height="48" viewBox="0 0 44 48" fill="none" stroke="var(--navy)" stroke-width="2.4"><rect x="3" y="8" width="38" height="30"/><path d="M3 15 H41"/><path d="M10 23 H20 M10 29 H16"/><path d="M26 22 L34 30 L30 31 L32 36 L30 37 L28 32 L25 34 Z" fill="var(--navy)"/></svg>
    <div><h3>Convenience of Online orders</h3><p>Class aptent taciti sociosqu ad litora torquent per conubia nostra per inceptos hymenaeos Proin nulla</p></div>
  </div>
  <div class="benefit" style="left:655px;top:275px">
    <svg width="44" height="48" viewBox="0 0 44 48" fill="none" stroke="var(--navy)" stroke-width="2.4"><rect x="6" y="8" width="32" height="24"/><path d="M1 36 H43"/><path d="M9 22 H16 L19 15 L23 28 L26 20 H35"/></svg>
    <div><h3>Order status monitoring</h3><p>Class aptent taciti sociosqu ad litora torquent per conubia nostra per inceptos hymenaeos Proin nulla</p></div>
  </div>
  <div class="benefit" style="left:132px;top:402px">
    <svg width="44" height="48" viewBox="0 0 44 48" fill="none" stroke="var(--navy)" stroke-width="2.4"><path d="M6 12 L38 20"/><circle cx="22" cy="12" r="3" fill="var(--navy)"/><path d="M6 12 L1 28 H13 Z M38 20 L33 34 H43 Z" fill="var(--navy)"/><path d="M22 15 V40 M14 40 H30"/></svg>
    <div><h3>Possibility to compare prices on the market</h3><p>Class aptent taciti sociosqu ad litora torquent per conubia nostra per inceptos hymenaeos Proin nulla</p></div>
  </div>
  <div class="benefit" style="left:655px;top:402px">
    <svg width="44" height="48" viewBox="0 0 44 48" fill="none" stroke="var(--navy)" stroke-width="2.4"><path d="M22 3 L40 9 V24 C40 35 32 42 22 46 C12 42 4 35 4 24 V9 Z"/><path d="M14 24 L20 30 L31 18"/></svg>
    <div><h3>Security and transparency of purchase</h3><p>Class aptent taciti sociosqu ad litora torquent per conubia nostra per inceptos hymenaeos Proin nulla</p></div>
  </div>
</section>

<section class="seller">
  <div class="seller-panel">
    <h2 class="heading">About benefits for Oil Seller</h2>
    <p class="lead">Duis quam Nam eget lacus Aliquam erat volutpat Quisque dignissim congue leo Mauris vel lacus vitae felis</p>
    <ul class="seller-list">
      <li>New sale channel</li>
      <li>Attracting new clients</li>
      <li>More oil sold</li>
      <li>Transaction security</li>
      <li>Possibility to integrate with distribution infrastructure and logistits for more efficient automation</li>
    </ul>
  </div>
  <div class="seller-photo" role="img" aria-label="Offshore oil platform with yellow crane boom at sunset over the sea"></div>
</section>

<section class="contact">
  <h2 class="heading section-title">Contact Form</h2>
  <div class="field" style="left:155px;top:140px;width:295px"><label>Your Name</label><div class="box"></div></div>
  <div class="field" style="left:459px;top:136px;width:295px"><label>Email address</label><div class="box"></div></div>
  <div class="field" style="left:762px;top:136px;width:295px"><label>Phone</label><div class="box"></div></div>
  <div class="field" style="left:155px;top:220px;width:902px"><label>Message</label><div class="box tall"></div></div>
  <span class="btn btn-submit">SUBMIT</span>
  <span class="btn btn-reset">RESET</span>
</section>

<footer class="site-footer">
  <div class="footer-col" style="left:117px"><h4>Company</h4><ul><li>About Us</li><li>What We Do</li><li>How it Works</li><li>Why Us</li></ul></div>
  <div class="footer-col" style="left:306px"><h4>Our Service</h4><ul><li>Sociosqu ad litora</li><li>Torquent per</li><li>Conubia nostra</li><li>Per inceptos</li></ul></div>
  <div class="footer-col" style="left:524px"><h4>Contact Us</h4><ul><li>415 Harbor Point Road Suite B12</li><li>Millbrook, OH 45820</li><li>(555) 014-7730</li><li>hello@crudeline-trade.com</li></ul>
    <div class="socials"><span></span><span></span><span></span><span></span></div>
  </div>
  <div class="brand footer-brand"><span class="brand-dot"></span>Crudeline</div>
  <div class="footer-legal">© 2016 Company Name All right reserved<br>Term of Use &nbsp;|&nbsp; Privacy Policy</div>
</footer>

</body>
</html>
```